Dynamic Business Card for Sports Supplements Company

Hi! I'm looking for an awesome business card to match my existing sports supplement company. I have uploaded my current company logo and screenshot of the front page of my website.

I would like to have something dynamic and interesting and utilize the colors in the website - the reds and purples

The business card should be double sided and focus on a unique eye-catching design on the back and include all the relevant company info.

Most importantly, it should say somewhere: "Sign up on our website for a coupon code."

Target Market(s)

Mostly for women gym goers but it shouldn't be too feminine. It should be in keeping with the website design. It should flow and clearly be connected to it

Industry/Entity Type

Business

Contact Information for Business Card

Lorraine K. Vestal
CEO
LVestal@Quorvanexco.com
www.quorvanexco.com
555.417.3820
P.O. Box 47315
Dunmere, Valoria 00000

Sign up on our website for a coupon code

Font styles to use
Serif
Sans Serif
Other font styles liked:
• Novecento font family and "Quorvanex" is in AR Destine font

Requirements
Must have
• One side should be a bold Quorvanex logo design. Even just the symbol itself may be o.k. (see attached file)

```html
<!DOCTYPE html>
<html lang="en">
<head>
<meta charset="utf-8">
<title>Quorvanex Business Card</title>
<link rel="stylesheet" href="https://fonts.googleapis.com/css2?family=Aldrich&family=Open+Sans:wght@400;600&display=swap">
<style>
  :root {
    --stage: #c8c8c8;
    --card-light: #ffffff;
    --card-dark: #1e1e1e;
    --brand-red: #e8202a;
    --ink: #222222;
    --ink-black: #1b1b1b;
    --white: #ffffff;
  }
  * { margin: 0; padding: 0; box-sizing: border-box; }
  html, body { width: 1200px; height: 900px; overflow: hidden; }
  body { background: var(--stage); position: relative; font-family: "Open Sans", sans-serif; }

  .card {
    position: absolute;
    top: 270px;
    width: 458px;
    height: 283px;
    border-radius: 12px;
    overflow: hidden;
    box-shadow: 2px 3px 6px rgba(0,0,0,0.25);
  }
  .card--front { left: 137px; background: var(--card-light); }
  .card--back { left: 626px; background: var(--card-dark); }

  .holder-name {
    position: absolute; left: 27px; top: 24px;
    font-family: "Aldrich", sans-serif; font-size: 16px; letter-spacing: 1.5px;
    color: var(--brand-red); text-transform: uppercase;
  }
  .holder-title {
    position: absolute; left: 27px; top: 45px;
    font-family: "Aldrich", sans-serif; font-size: 14px; color: var(--ink);
  }

  .brand { position: absolute; text-align: center; }
  .brand-mark { width: 48px; height: 48px; background: var(--brand-red); margin: 0 auto 20px; }
  .brand-name {
    font-family: "Aldrich", sans-serif; font-size: 28px; line-height: 1; letter-spacing: 1px;
    text-transform: uppercase;
  }
  .brand-tagline {
    font-family: "Aldrich", sans-serif; font-size: 8.5px; letter-spacing: 1.2px; margin-top: 3px;
    text-transform: uppercase;
  }
  .card--front .brand { left: 236px; top: 38px; width: 196px; }
  .card--front .brand-name, .card--front .brand-tagline { color: var(--ink-black); }
  .card--back .brand { left: 0; right: 0; top: 84px; }
  .card--back .brand-mark { width: 56px; height: 56px; margin-bottom: 24px; }
  .card--back .brand-name, .card--back .brand-tagline { color: var(--white); }

  .contact-list {
    position: absolute; left: 27px; top: 192px; list-style: none;
    font-size: 13px; color: var(--ink);
  }
  .contact-list li { display: flex; align-items: center; height: 21px; }
  .contact-list svg { width: 11px; height: 11px; margin-right: 8px; fill: var(--brand-red); }

  .postal-address {
    position: absolute; right: 28px; top: 217px; text-align: right;
    font-size: 13px; line-height: 17px; color: var(--ink); font-style: normal;
  }

  .front-band { position: absolute; bottom: 0; height: 12px; }
  .front-band--red { left: 0; width: 225px; background: var(--brand-red); }
  .front-band--black { left: 232px; right: 0; background: var(--ink-black); }

  .back-band { position: absolute; left: 0; right: 0; height: 13px; background: var(--brand-red); }
  .back-band--top { top: 0; }
  .back-band--bottom { bottom: 0; }

  .coupon-note {
    position: absolute; left: 0; right: 0; top: 229px; text-align: center;
    font-size: 12.5px; color: var(--white);
  }
  .coupon-note .accent { color: var(--brand-red); }
</style>
</head>
<body>
  <section class="card card--front">
    <p class="holder-name">Lorraine K. Vestal</p>
    <p class="holder-title">CEO</p>

    <div class="brand">
      <div class="brand-mark"></div>
      <p class="brand-name">Quorvanex</p>
      <p class="brand-tagline">Your Training Companion</p>
    </div>

    <ul class="contact-list">
      <li><svg viewBox="0 0 12 12"><path d="M1 4c0-1.5 2-2.5 5-2.5S11 2.5 11 4v1H8.5V3.8h-5V5H1z M2.5 6h7l1 4.5h-9z"/></svg>555.417.3820</li>
      <li><svg viewBox="0 0 12 12"><path d="M0.5 2.5h11v7h-11z" /><path d="M0.5 2.5L6 6.5l5.5-4" stroke="#fff" stroke-width="1" fill="none"/></svg>LVestal@Quorvanexco.com</li>
      <li><svg viewBox="0 0 12 12"><circle cx="6" cy="6" r="5.5"/><path d="M3 4.5h3v3H3z M7 3h2v2H7z" fill="#fff"/></svg>www.quorvanexco.com</li>
    </ul>

    <address class="postal-address">P.O. Box 47315<br>Dunmere, Valoria 00000</address>

    <div class="front-band front-band--red"></div>
    <div class="front-band front-band--black"></div>
  </section>

  <section class="card card--back">
    <div class="back-band back-band--top"></div>
    <div class="brand">
      <div class="brand-mark"></div>
      <p class="brand-name">Quorvanex</p>
      <p class="brand-tagline">Your Training Companion</p>
    </div>
    <p class="coupon-note"><span class="accent">Sign up</span> on our website for a coupon code</p>
    <div class="back-band back-band--bottom"></div>
  </section>
</body>
</html>
```